Business Card Design

We need a design for business cards for our company. We have a logo. We teach EMT's and we are based out of Virginia. The information that will need to add would be, name, title, phone number, email, address. On the back of the business card would be "We help you, help others"

Target Market(s)

People that want to become EMT's

Colors

Designer to choose colors to be used in the design.

Requirements
Must have
• company logo

```html
<!DOCTYPE html>
<html lang="en">
<head>
<meta charset="utf-8">
<title>Halvern Rescue Academy – Business Card</title>
<link rel="stylesheet" href="https://fonts.googleapis.com/css2?family=Arimo:wght@400&display=swap">
<style>
  :root {
    --ink: #2f3237;
    --slate: #212b35;
    --accent: #ee2b47;
    --accent-deep: #b51d33;
    --paper: #ffffff;
    --paper-shade: #e6e7ea;
  }
  html, body {
    margin: 0;
    padding: 0;
    width: 1200px;
    height: 686px;
    overflow: hidden;
    background: var(--paper);
  }
  .card {
    position: relative;
    width: 1200px;
    height: 686px;
    overflow: hidden;
    font-family: "Arimo", Arial, sans-serif;
    color: var(--ink);
    background: radial-gradient(ellipse at 75% 50%, var(--paper) 40%, var(--paper-shade) 100%);
  }
  .card-shapes {
    position: absolute;
    inset: 0;
    width: 1200px;
    height: 686px;
  }
  .brand {
    position: absolute;
    left: 50px;
    top: 280px;
    display: flex;
    align-items: center;
    gap: 18px;
  }
  .brand-dot {
    width: 24px;
    height: 24px;
    border-radius: 50%;
    background: var(--accent);
    flex: none;
  }
  .brand-name {
    margin: 0;
    font-size: 52px;
    font-weight: 400;
    line-height: 60px;
    letter-spacing: 1px;
    color: var(--accent);
    text-transform: uppercase;
  }
  .identity {
    position: absolute;
    left: 790px;
    top: 178px;
    padding-left: 12px;
    border-left: 13px solid var(--accent);
    line-height: 1;
  }
  .identity-name {
    margin: 0;
    font-size: 41px;
    font-weight: 400;
    line-height: 48px;
  }
  .identity-name .surname { color: var(--accent); }
  .identity-title {
    margin: 0;
    font-size: 41px;
    font-weight: 400;
    line-height: 48px;
  }
  .contacts {
    position: absolute;
    left: 766px;
    top: 302px;
    margin: 0;
    padding: 0;
    list-style: none;
    font-size: 30px;
    line-height: 38px;
  }
  .contact {
    display: flex;
    align-items: flex-start;
    margin-bottom: 13px;
  }
  .contact-icon {
    width: 30px;
    height: 30px;
    margin-top: 5px;
    margin-right: 22px;
    flex: none;
  }
</style>
</head>
<body>
<main class="card">
  <svg class="card-shapes" viewBox="0 0 1400 800" aria-hidden="true">
    <polygon points="0,0 655,0 820,238 690,570 620,800 0,800" fill="var(--slate)"/>
    <polygon points="655,0 895,0 820,238" fill="var(--accent)"/>
    <polygon points="690,566 720,592 700,640" fill="var(--accent-deep)"/>
    <polygon points="700,590 620,800 880,800" fill="var(--accent)"/>
  </svg>

  <div class="brand">
    <span class="brand-dot"></span>
    <p class="brand-name">Halvern Rescue<br>Academy</p>
  </div>

  <div class="identity">
    <h1 class="identity-name">Daniel <span class="surname">Hartley</span></h1>
    <p class="identity-title">Director</p>
  </div>

  <ul class="contacts">
    <li class="contact">
      <svg class="contact-icon" viewBox="0 0 30 30" aria-hidden="true">
        <rect x="10" y="2" width="13" height="25" rx="2" fill="var(--accent)"/>
        <rect x="12.5" y="6" width="8" height="15" fill="var(--paper)"/>
        <path d="M4 14 q2 -3 6 -1 v9 q-4 2 -6 -1 z" fill="var(--accent)"/>
      </svg>
      <span>0500 44 67890</span>
    </li>
    <li class="contact">
      <svg class="contact-icon" viewBox="0 0 30 30" aria-hidden="true">
        <rect x="2" y="8" width="26" height="17" fill="var(--accent)"/>
        <path d="M2 8 L15 18 L28 8" fill="none" stroke="var(--paper)" stroke-width="2"/>
      </svg>
      <span>Info@halvernrescue.com</span>
    </li>
    <li class="contact">
      <svg class="contact-icon" viewBox="0 0 30 30" aria-hidden="true">
        <circle cx="15" cy="15" r="12" fill="var(--accent)"/>
        <rect x="2" y="12" width="26" height="7" fill="var(--paper)"/>
        <text x="15" y="18" text-anchor="middle" font-size="6.5" font-family="Arimo, Arial, sans-serif" fill="var(--accent)">www</text>
      </svg>
      <span>www.halvernrescue.com</span>
    </li>
    <li class="contact">
      <svg class="contact-icon" viewBox="0 0 30 30" aria-hidden="true">
        <path d="M3 27 L7 19 H23 L27 27 Z" fill="none" stroke="var(--accent)" stroke-width="1.6"/>
        <path d="M15 22 C10 15 9 13 9 10 a6 6 0 0 1 12 0 c0 3 -1 5 -6 12 z" fill="var(--accent)"/>
        <circle cx="15" cy="10" r="2.4" fill="var(--paper)"/>
      </svg>
      <span>2207/45 kessel street,<br>easton qld 4100</span>
    </li>
  </ul>
</main>
</body>
</html>
```